Phuket Thailand - Rental Villa Website

I have a villa for rent in Thailand and require a website - i need to demo pictures/walk through video, local attractions, villa facilities description plus seaonal rates and online booking.

Industry/Entity Type

Rental

Coding

Coded - Design and coding required

```html
<!DOCTYPE html>
<html lang="en">
<head>
<meta charset="utf-8">
<title>Palm Haven</title>
<link rel="stylesheet" href="https://fonts.googleapis.com/css2?family=Questrial&family=Open+Sans:ital,wght@0,400;0,600;1,400&display=swap">
<style>
:root{
  --red:#d9303a;
  --navy:#1f2735;
  --navy-2:#2c3a4f;
  --page:#edf0f4;
  --white:#ffffff;
  --ink:#1b1f27;
  --muted:#9aa1ab;
  --footer-text:#7f8896;
}
*{box-sizing:border-box;margin:0;padding:0}
html,body{width:1200px;height:2490px;overflow:hidden}
body{background:var(--page);font-family:"Open Sans",sans-serif;color:var(--ink);position:relative}
.topbar{height:33px;background:var(--navy);display:flex;align-items:center;justify-content:space-between;padding:0 60px;font-size:10px;color:var(--footer-text)}
.topbar .info{display:flex;align-items:center;gap:8px}
.topbar .sep{margin:0 6px}
.topbar .social{display:flex;gap:10px}
.topbar .social span{width:7px;height:7px;border-radius:50%;background:var(--footer-text);display:block}
.header{height:85px;display:flex;align-items:center;justify-content:space-between;padding:0 60px;background:var(--page)}
.logo{font-family:"Questrial",sans-serif;font-size:30px;font-weight:400;color:var(--ink);display:flex;align-items:center;gap:10px}
.logo-mark{width:14px;height:14px;background:var(--red);display:block}
.nav{display:flex;height:100%}
.nav a{font-family:"Questrial",sans-serif;font-size:15px;color:var(--ink);text-decoration:none;display:flex;align-items:center;padding:0 23px;position:relative;height:100%}
.nav a.active{color:var(--red)}
.nav a.active::after{content:"";position:absolute;left:0;right:0;bottom:0;height:4px;background:var(--red)}
.nav a:last-child{padding-right:0}
.hero{position:relative;height:499px;background:linear-gradient(100deg,#3b3230 0%,#5b524c 30%,#7a736c 50%,#4e4a45 70%,#2d2a29 100%)}
.hero-title{position:absolute;left:60px;top:187px;background:var(--red);color:var(--white);font-family:"Questrial",sans-serif;font-size:36px;padding:0 25px;height:77px;width:255px;display:flex;align-items:center}
.hero-sub{position:absolute;left:60px;top:266px;width:383px;height:80px;background:rgba(31,39,53,.92);color:#aeb5c0;font-size:22px;display:flex;align-items:center;padding:0 22px}
.dots{position:absolute;top:470px;left:567px;display:flex;gap:14px}
.dots span{width:13px;height:13px;border-radius:50%;background:#b9bcc1;display:block}
.dots span.on{background:var(--red)}
.booking{height:132px;background:var(--navy);display:flex;align-items:center;padding:0 60px;gap:16px}
.field{width:219px;height:47px;background:var(--navy-2);color:#b9c0cb;font-size:12px;display:flex;align-items:center;padding:0 16px}
.book-btn{width:141px;height:47px;background:var(--red);color:var(--white);font-family:"Questrial",sans-serif;font-size:22px;display:flex;align-items:center;justify-content:center}
.shadow{height:26px;margin:0 auto;width:860px;background:radial-gradient(ellipse at top,rgba(0,0,0,.35) 0%,rgba(0,0,0,0) 70%)}
.section-title{font-family:"Questrial",sans-serif;font-weight:400;font-size:29px;text-align:center;color:var(--ink);letter-spacing:.5px}
.rates-title{margin-top:46px}
.rates{margin:40px 61px 0;display:grid;grid-template-columns:repeat(4,269.5px);grid-template-rows:repeat(4,240.25px)}
.photo{display:block}
.feature{grid-column:1/3;grid-row:1/3;position:relative;background:linear-gradient(170deg,#2b3447 0%,#3c4556 45%,#2a2a2c 75%,#1d1d1f 100%)}
.feature-body{position:absolute;left:34px;right:34px;bottom:38px;color:var(--white)}
.feature-head{display:flex;justify-content:space-between;align-items:flex-start}
.feature-name{font-family:"Questrial",sans-serif;font-size:30px;line-height:1.3;width:360px}
.feature-price{font-family:"Questrial",sans-serif;font-size:30px}
.feature-desc{font-size:12.5px;color:#b7bcc4;margin-top:16px;line-height:1.4;width:470px}
.feature .rating{color:#c8ccd3;margin-top:22px;font-size:12.5px}
.card{background:var(--white);padding:20px 30px 0}
.card-name{font-family:"Questrial",sans-serif;font-size:25px;line-height:1.35;color:var(--ink)}
.card-desc{font-size:12px;color:var(--muted);line-height:1.35;margin-top:16px}
.card-price{font-family:"Questrial",sans-serif;font-size:25px;color:var(--red);margin-top:14px}
.rating{font-family:"Questrial",sans-serif;font-size:16px;margin-top:10px;color:var(--ink)}
.stars{color:var(--red);letter-spacing:1px;font-size:14px}
.stars .off{color:var(--ink)}
.testimonial-title{margin-top:28px}
.testimonials{display:flex;justify-content:space-between;margin:38px 58px 0 60px}
.quote{width:520px;height:158px;background:var(--white);display:flex}
.quote .photo{width:179px;height:158px;flex:none}
.quote-body{padding:42px 30px 0}
.quote-text{font-size:12.5px;color:var(--muted);line-height:1.3}
.quote-name{font-style:italic;font-size:13px;color:var(--ink);margin-top:12px}
.footer{position:absolute;left:0;right:0;top:2188px;bottom:0;background:var(--navy)}
.footer-cols{position:relative;height:237px}
.footer-col{position:absolute;top:42px}
.footer-col h3{font-family:"Questrial",sans-serif;font-weight:400;font-size:21px;color:var(--white);margin-bottom:20px}
.footer-col li{list-style:none;font-size:12px;color:var(--footer-text);line-height:22px;display:flex;align-items:center;gap:9px}
.footer-col p{font-size:12px;color:var(--footer-text);line-height:22px}
.footer-col .sq{width:10px;height:10px;background:var(--footer-text);display:block}
.footer-bottom{border-top:1px solid #2f394a;height:65px;display:flex;align-items:center;justify-content:center;font-size:11px;color:#5f6878}
</style>
</head>
<body>
<div class="topbar">
  <div class="info">
    <svg width="8" height="11" viewBox="0 0 8 11"><path d="M4 0C1.8 0 0 1.7 0 3.9 0 6.8 4 11 4 11s4-4.2 4-7.1C8 1.7 6.2 0 4 0zm0 5.4a1.5 1.5 0 110-3 1.5 1.5 0 010 3z" fill="#7f8896"/></svg>
    <span>Lorem ipsum dolor sit amet, consectetur adipiscing elit</span>
    <span class="sep">|</span>
    <svg width="7" height="11" viewBox="0 0 7 11"><rect x="0.5" y="0.5" width="6" height="10" rx="1" fill="none" stroke="#7f8896"/><rect x="2.5" y="8.3" width="2" height="1" fill="#7f8896"/></svg>
    <span>1800-555-014</span>
  </div>
  <div class="social"><span></span><span></span><span></span></div>
</div>

<header class="header">
  <div class="logo"><span class="logo-mark"></span>Palm Haven</div>
  <nav class="nav">
    <a class="active">Home</a>
    <a>About us</a>
    <a>Properties</a>
    <a>Booking</a>
    <a>Gallery</a>
    <a>Contact us</a>
  </nav>
</header>

<section class="hero" role="img" aria-label="Photo of a villa bedroom interior with artwork on the wall and a window to the garden">
  <div class="hero-title">Luxury Villa</div>
  <div class="hero-sub">Et ultricies tortor commodo et....</div>
  <div class="dots"><span></span><span class="on"></span><span></span></div>
</section>

<section class="booking">
  <div class="field">First Name</div>
  <div class="field">Last Name</div>
  <div class="field">Email Id</div>
  <div class="field">Phone Number</div>
  <div class="book-btn">Book Now</div>
</section>
<div class="shadow"></div>

<h2 class="section-title rates-title">SEASONAL RATES</h2>
<section class="rates">
  <div class="feature" role="img" aria-label="Photo of a modern villa at dusk with palm trees">
    <div class="feature-body">
      <div class="feature-head">
        <div class="feature-name">Luxury Villa, Kata Road, Phuket</div>
        <div class="feature-price">$ 420</div>
      </div>
      <p class="feature-desc">Cras varius ornare ante, et ultricies tortor commodo et. Pellentesque non massa eget lorem dictum mollis.</p>
      <div class="rating">Rating : <span class="stars">★★★★<span class="off">★</span></span></div>
    </div>
  </div>
  <div class="photo" role="img" aria-label="Photo of a stone terrace with a wooden pavilion and mountain view" style="background:linear-gradient(170deg,#b9c2c9 0%,#7d8a7a 40%,#c7c1b6 70%,#9a938a 100%)"></div>
  <div class="card">
    <div class="card-name">Luxury Family<br>House</div>
    <p class="card-desc">Cras varius ornare ante, et ultricies tortor commodo et....</p>
    <div class="card-price">$ 420</div>
    <div class="rating">Rating : <span class="stars">★★★★<span class="off">★</span></span></div>
  </div>
  <div class="card">
    <div class="card-name">Luxury Family<br>House</div>
    <p class="card-desc">Cras varius ornare ante, et ultricies tortor commodo et....</p>
    <div class="card-price">$ 420</div>
    <div class="rating">Rating : <span class="stars">★★★★<span class="off">★</span></span></div>
  </div>
  <div class="photo" role="img" aria-label="Photo of a villa roof corner with tropical plants" style="background:linear-gradient(160deg,#6f5a55 0%,#8a7f78 40%,#4b5a46 75%,#3d4a38 100%)"></div>
  <div class="photo" role="img" aria-label="Photo of an open-plan living and dining room" style="background:linear-gradient(160deg,#c9c6c2 0%,#8d7f74 45%,#5a4c44 75%,#7b7b82 100%)"></div>
  <div class="card">
    <div class="card-name">Luxury Family<br>House</div>
    <p class="card-desc">Cras varius ornare ante, et ultricies tortor commodo et....</p>
    <div class="card-price">$ 420</div>
    <div class="rating">Rating : <span class="stars">★★★★<span class="off">★</span></span></div>
  </div>
  <div class="photo" role="img" aria-label="Photo of a timber-roofed sala overlooking a pool" style="background:linear-gradient(170deg,#4a2f22 0%,#6b4a35 40%,#7f8f86 70%,#5b6d68 100%)"></div>
  <div class="card">
    <div class="card-name">Luxury Family<br>House</div>
    <p class="card-desc">Cras varius ornare ante, et ultricies tortor commodo et....</p>
    <div class="card-price">$ 420</div>
    <div class="rating">Rating : <span class="stars">★★★★<span class="off">★</span></span></div>
  </div>
  <div class="card">
    <div class="card-name">Luxury Family<br>House</div>
    <p class="card-desc">Cras varius ornare ante, et ultricies tortor commodo et....</p>
    <div class="card-price">$ 420</div>
    <div class="rating">Rating : <span class="stars">★★★★<span class="off">★</span></span></div>
  </div>
  <div class="photo" role="img" aria-label="Photo of an infinity pool with hills in the distance" style="background:linear-gradient(175deg,#aab4b8 0%,#8f9a98 30%,#6f9a8c 60%,#4e8a7a 100%)"></div>
  <div class="card">
    <div class="card-name">Luxury Family<br>House</div>
    <p class="card-desc">Cras varius ornare ante, et ultricies tortor commodo et....</p>
    <div class="card-price">$ 420</div>
    <div class="rating">Rating : <span class="stars">★★★★<span class="off">★</span></span></div>
  </div>
  <div class="photo" role="img" aria-label="Photo of a bright lounge with white sofas and framed pictures" style="background:linear-gradient(175deg,#e6e4e0 0%,#d4d0ca 50%,#a88d6e 80%,#8c7257 100%)"></div>
</section>
<div class="shadow" style="margin-top:6px"></div>

<h2 class="section-title testimonial-title">TESTIMONIAL</h2>
<section class="testimonials">
  <article class="quote">
    <div class="photo" role="img" aria-label="Photo of a smartly dressed couple at an evening event" style="background:linear-gradient(135deg,#6b4a2a 0%,#3a2a1f 50%,#1c1612 100%)"></div>
    <div class="quote-body">
      <p class="quote-text">Nemo enim ipsam voluptatem quia voluptas sit aspernatur aut odit aut fugit.</p>
      <p class="quote-name">Joe Bloggs</p>
    </div>
  </article>
  <article class="quote">
    <div class="photo" role="img" aria-label="Photo of two business people in front of office buildings" style="background:linear-gradient(135deg,#e8edf2 0%,#9fb3c6 45%,#2d3440 100%)"></div>
    <div class="quote-body">
      <p class="quote-text">Nemo enim ipsam voluptatem quia voluptas sit aspernatur aut odit aut fugit.</p>
      <p class="quote-name">Jane Bloggs</p>
    </div>
  </article>
</section>

<footer class="footer">
  <div class="footer-cols">
    <div class="footer-col" style="left:60px">
      <h3>QUICK LINKS</h3>
      <ul><li>Home</li><li>About us</li><li>Properties</li><li>Booking</li><li>Gallery</li></ul>
    </div>
    <div class="footer-col" style="left:300px">
      <h3>CUSTOMER SUPPORT</h3>
      <ul><li>Support</li><li>Online Booking</li><li>Features</li><li>Local attractions</li><li>Contact us</li></ul>
    </div>
    <div class="footer-col" style="left:606px;width:260px">
      <h3>CONTACT US</h3>
      <p>Lorem ipsum dolor sit amet, consectetur adipiscing elit.</p>
      <p style="margin-top:22px">800 555-01-29 &nbsp;&nbsp;|&nbsp;&nbsp; info@palmhaven.com</p>
    </div>
    <div class="footer-col" style="left:941px">
      <h3>CONNECT WITH US</h3>
      <ul><li><span class="sq"></span>Community</li><li><span class="sq"></span>Updates</li><li><span class="sq"></span>Rss</li></ul>
    </div>
  </div>
  <div class="footer-bottom">© 2015 &nbsp;Palm Haven. All rights reserved.</div>
</footer>
</body>
</html>
```